Brovanek Data Yellow rose letterhead

I have a new logo for my company but in its current form it is too large to be used on letterhead or as a email signature. I need to have the designer use elements from the current logo and create something close to the original but more suited for smaller items.
Updates

I just uploaded a copy of our logo that does not have the weathered affect. Thanks

Reason: More time for revisions

Industry/Entity Type

It Company

Requirements
Must have
• The design must maintain the visual effect of the current logo. It needs to include the yellow rose and the name of the company.
Nice to have
• It would be nice to maintain the stamp theme and incorporate my name, address, phone, email. etc.

```html
<!DOCTYPE html>
<html lang="en">
<head>
<meta charset="utf-8">
<title>Brovanek Data Letterhead</title>
<link rel="stylesheet" href="https://fonts.googleapis.com/css2?family=Questrial&display=swap">
<style>
  :root {
    --backdrop: #d6d4d5;
    --paper: #ffffff;
    --earth-brown: #594a42;
    --rose-yellow: #f6c430;
    --ink: #111111;
    --on-brown: #ffffff;
  }
  * { box-sizing: border-box; margin: 0; padding: 0; }
  html, body {
    width: 848px;
    height: 1200px;
    overflow: hidden;
    background: var(--backdrop);
  }
  .letterhead {
    position: absolute;
    left: 96px;
    top: 116px;
    width: 658px;
    height: 930px;
    background: var(--paper);
    overflow: hidden;
    font-family: "Questrial", "Century Gothic", sans-serif;
  }
  .brand-block {
    position: absolute;
    left: 222px;
    top: 0;
    width: 203px;
    height: 197px;
    background: var(--earth-brown);
    display: flex;
    flex-direction: column;
    align-items: center;
    justify-content: center;
    gap: 18px;
  }
  .brand-dot {
    width: 86px;
    height: 86px;
    border-radius: 50%;
    background: var(--rose-yellow);
  }
  .brand-name {
    color: var(--on-brown);
    font-size: 22px;
    letter-spacing: 0.5px;
    text-align: center;
  }
  .sender {
    position: absolute;
    left: 22px;
    top: 796px;
    font-size: 15px;
    line-height: 20.5px;
    color: var(--ink);
    font-style: normal;
    letter-spacing: 0.2px;
  }
  .footer-wave {
    position: absolute;
    left: 0;
    bottom: 0;
    width: 658px;
    height: 60px;
    display: block;
  }
  .footer-wave path { fill: var(--earth-brown); }
</style>
</head>
<body>
  <main class="letterhead">
    <header class="brand-block">
      <span class="brand-dot" aria-hidden="true"></span>
      <span class="brand-name">Brovanek Data</span>
    </header>

    <address class="sender">
      Mara Quillen, PhD<br>
      218 W Cedar Ridge Road, Ste 1140<br>
      Elm Falls, TX 75990<br>
      1-800-555-0147<br>
      mara@brovanek-data.com
    </address>

    <svg class="footer-wave" viewBox="0 0 658 60" preserveAspectRatio="none" aria-hidden="true">
      <path d="M0 36 Q 330 58 658 7 L658 60 L0 60 Z"/>
    </svg>
  </main>
</body>
</html>
```